Smile first. Sign later.

Sub: how quiet warmth wins every deal.

The book talks about what you need to do to achieves a better atmosphere and what you need to do warm your customer. It provides techniques on how to talk, move and about how to create rapport using content, hobbies, common interests and so on. All to increase success in selling something, convincing somebody and being liked much more. It extends to the claim that convincing your spouse to chose your favorite movie rather than hers or to pick that vacation sport over the other one would also a sale, not a commercial sale but an important one too. And that you can achieve these kind of success too using the information from the book. However this is NOT a self help book but a business book!

```html
<!DOCTYPE html>
<html lang="en">
<head>
<meta charset="utf-8">
<title>Smile First. Sign Later. — Book Cover</title>
<link rel="stylesheet" href="https://fonts.googleapis.com/css2?family=Poppins:wght@200;300;400&display=swap">
<style>
  :root {
    --cover-cyan: #21c1d9;
    --ink-black: #0b0b0b;
    --paper-white: #ffffff;
  }
  html, body {
    margin: 0;
    padding: 0;
    width: 802px;
    height: 1200px;
    overflow: hidden;
    background: var(--cover-cyan);
  }
  .cover {
    position: relative;
    width: 802px;
    height: 1200px;
    background: var(--cover-cyan);
    overflow: hidden;
    font-family: "Poppins", sans-serif;
  }
  .pointing-hand, .business-team {
    position: absolute;
    left: 0;
    display: block;
  }
  .pointing-hand { top: 200px; }
  .business-team { top: 880px; }
  .title {
    margin: 0;
    font-weight: 200;
    color: var(--ink-black);
  }
  .title span {
    position: absolute;
    left: 0;
    width: 802px;
    text-align: center;
    line-height: 1;
    white-space: nowrap;
  }
  .title-line-one { top: 4px; font-size: 166px; letter-spacing: 4px; }
  .title-line-two { top: 167px; font-size: 186px; letter-spacing: 4px; color: var(--paper-white); }
  .title-line-three { top: 354px; font-size: 103px; letter-spacing: 6px; }
  .title-line-four { top: 451px; font-size: 90px; letter-spacing: 6px; }
  .author {
    position: absolute;
    top: 572px;
    left: 314px;
    margin: 0;
    font-size: 29px;
    font-weight: 400;
    line-height: 1;
    color: var(--ink-black);
    white-space: nowrap;
  }
  .subtitle {
    position: absolute;
    top: 728px;
    left: 446px;
    margin: 0;
    font-size: 33px;
    font-weight: 300;
    line-height: 47px;
    letter-spacing: 3px;
    color: var(--paper-white);
    white-space: nowrap;
  }
</style>
</head>
<body>
<main class="cover">
  <svg class="pointing-hand" width="390" height="680" viewBox="0 0 390 680" role="img" aria-label="Illustration of a suited arm reaching in from the left, its hand pointing down at one person">
    <defs>
      <linearGradient id="hand-tone" x1="0" y1="0" x2="1" y2="0">
        <stop offset="0" stop-color="#0b0b0b"/>
        <stop offset="0.45" stop-color="#0b0b0b" stop-opacity="0.75"/>
        <stop offset="1" stop-color="#21c1d9" stop-opacity="0"/>
      </linearGradient>
    </defs>
    <rect x="0" y="0" width="390" height="680" fill="url(#hand-tone)"/>
  </svg>

  <h1 class="title">
    <span class="title-line-one">SMILE</span>
    <span class="title-line-two">FIRST.</span>
    <span class="title-line-three">SIGN</span>
    <span class="title-line-four">LATER.</span>
  </h1>

  <p class="author">Marten Halloway</p>

  <p class="subtitle">how quiet warmth<br>wins every<br>deal.</p>

  <svg class="business-team" width="802" height="320" viewBox="0 0 802 320" role="img" aria-label="Silhouettes of five business people standing in a row, the centre one highlighted in white">
    <defs>
      <linearGradient id="team-tone" x1="0" y1="0" x2="0" y2="1">
        <stop offset="0" stop-color="#21c1d9"/>
        <stop offset="0.4" stop-color="#0f5f6c"/>
        <stop offset="1" stop-color="#0b0b0b"/>
      </linearGradient>
    </defs>
    <rect x="0" y="0" width="802" height="320" fill="url(#team-tone)"/>
    <rect x="0" y="310" width="802" height="10" fill="#0b0b0b"/>
  </svg>
</main>
</body>
</html>
```